Business Card Design for Flood Rescue 360 - Property Restoration Professionals

I need a business card designed for Flood Rescue 360. We are a full-service property restoration solution. Providing water, fire, smoke & storm restoration as well as mold remediation and full remodel or reconstruction to homes and businesses across Dallas-Fort Worth, TX.
Target Market(s)
home and business owners with insurance covered property damage from water, fire or storm related damage
Industry/Entity Type
property restoration
Contact Information for Business Card
Marcus Pelley General Manager Cell: 214-555-0193 Office: 469-555-0148 email: Marcus@FloodRescue360.example services: Water, Fire, Mold, Reconstruction Tagline: Urgency for Your Water Emergency!
Look and feel
Each slider illustrates characteristics of the customer's brand and the style your logo design should communicate.

```html
<!DOCTYPE html>
<html lang="en">
<head>
<meta charset="utf-8">
<title>Flood Rescue 360 – Business Card</title>
<link href="https://fonts.googleapis.com/css2?family=Roboto:wght@400;500;900&display=swap" rel="stylesheet">
<style>
  :root {
    --stage: #121212;
    --brand-blue: #0fb2e4;
    --band-blue: #1ab5e6;
    --white: #ffffff;
    --ink: #1b1b1b;
    --grey: #7a7a7a;
  }
  * { margin: 0; padding: 0; box-sizing: border-box; }
  html, body { width: 1200px; height: 960px; overflow: hidden; background: var(--stage); }
  body { position: relative; font-family: "Roboto", Arial, sans-serif; }

  .card {
    position: absolute;
    left: 249px;
    width: 702px;
    height: 401px;
    overflow: hidden;
    box-shadow: 0 12px 30px rgba(0,0,0,.6);
  }
  .card--front { top: 60px; background: var(--brand-blue); }
  .card--back { top: 500px; background: var(--white); }

  /* front */
  .front-brand {
    position: absolute;
    left: 0; right: 0; top: 132px;
    text-align: center;
    font-weight: 900; font-size: 72px; line-height: .95;
    color: var(--white); text-transform: uppercase; letter-spacing: .5px;
  }

  .services { position: absolute; left: 0; right: 0; top: 336px; text-align: center; color: var(--white); }
  .services__heading {
    display: flex; align-items: center; justify-content: center; gap: 8px;
    font-weight: 500; font-size: 17px; letter-spacing: .3px;
  }
  .services__rule { width: 122px; height: 2px; background: var(--white); border-radius: 1px; }
  .services__list {
    margin-top: 4px; list-style: none;
    display: flex; justify-content: center; gap: 8px;
    font-size: 17px; letter-spacing: .4px;
  }
  .services__list li { display: flex; align-items: center; gap: 6px; }
  .services__list li::before {
    content: ""; width: 9px; height: 9px; border-radius: 50%;
    border: 2px solid var(--white);
  }

  /* back */
  .back-brand {
    position: absolute; left: 28px; top: 26px;
    font-weight: 900; font-size: 58px; line-height: .95;
    color: var(--brand-blue); text-transform: uppercase;
  }

  .holder { position: absolute; right: 30px; top: 26px; text-align: right; }
  .holder__name { font-weight: 500; font-size: 38px; line-height: 1; color: var(--grey); }
  .holder__first { color: var(--brand-blue); }
  .holder__title { margin-top: 4px; font-size: 18px; color: var(--ink); letter-spacing: .3px; }
  .holder-tab { position: absolute; right: 0; top: 32px; width: 19px; height: 53px; background: var(--brand-blue); }

  .tagline { position: absolute; left: 28px; top: 256px; font-size: 18px; color: var(--brand-blue); letter-spacing: .3px; }

  .contact-band { position: absolute; left: 0; right: 0; top: 295px; height: 106px; background: var(--band-blue); }
  .contact-list { position: absolute; left: 28px; top: 14px; list-style: none; color: var(--white); font-size: 17px; letter-spacing: .6px; }
  .contact-list li { display: flex; align-items: center; gap: 12px; height: 23.5px; }
  .contact-list svg { width: 15px; height: 15px; flex: none; }
</style>
</head>
<body>

<section class="card card--front" aria-label="Card front">
  <p class="front-brand">Flood<br>Rescue 360</p>
  <div class="services">
    <p class="services__heading"><span class="services__rule"></span>SERVICES<span class="services__rule"></span></p>
    <ul class="services__list">
      <li>Water</li><li>Fire</li><li>Mold</li><li>Reconstruction</li>
    </ul>
  </div>
</section>

<section class="card card--back" aria-label="Card back">
  <p class="back-brand">Flood<br>Rescue 360</p>

  <div class="holder">
    <p class="holder__name"><span class="holder__first">Marcus</span> Pelley</p>
    <p class="holder__title">General Manager</p>
  </div>
  <span class="holder-tab" aria-hidden="true"></span>

  <p class="tagline">Urgency for Your Water Emergency!</p>

  <div class="contact-band">
    <ul class="contact-list">
      <li>
        <svg viewBox="0 0 16 16" aria-hidden="true"><rect x="4" y="1" width="8" height="14" rx="1.5" fill="none" stroke="#fff" stroke-width="1.6"/></svg>
        214-555-0193
      </li>
      <li>
        <svg viewBox="0 0 16 16" aria-hidden="true"><path d="M3 2l3 0 1 3-2 1.5c1 2 2.5 3.5 4.5 4.5L11 9l3 1v3c0 .6-.4 1-1 1C7 14 2 9 2 3c0-.6.4-1 1-1z" fill="#fff"/></svg>
        469-555-0148
      </li>
      <li>
        <svg viewBox="0 0 16 16" aria-hidden="true"><rect x="1" y="4" width="14" height="10" rx="1" fill="#fff"/><path d="M1 5l7 5 7-5" fill="none" stroke="#1ab5e6" stroke-width="1.4"/></svg>
        Marcus@FloodRescue360.example
      </li>
    </ul>
  </div>
</section>

</body>
</html>
```